Flag Order

We were just looking to order some branding flags to put on our rental equipment for our business. We would like different examples of the colors, shapes, sizes, backgrounds etc. Was thinking of just doing the plains icon instead of the whole logo on there. but open to ideas. preferably not a white background as they could get dirty,

```html
<!DOCTYPE html>
<html lang="en">
<head>
<meta charset="utf-8">
<title>Mesa Equipment Rentals – Feather Flag</title>
<link rel="stylesheet" href="https://fonts.googleapis.com/css2?family=Montserrat:wght@700&display=swap">
<style>
  :root {
    --backdrop: #555555;
    --flag-black: #2b2c2e;
    --flag-sleeve: #1c1c1d;
    --flag-blue: #3f8fd6;
    --flag-blue-deep: #2f7fc8;
    --text-white: #ffffff;
    --photo-top: #8fb3cf;
    --photo-mid: #d9b27a;
    --photo-low: #9a8468;
  }
  html, body {
    margin: 0;
    padding: 0;
    width: 1200px;
    height: 1200px;
    overflow: hidden;
    background: var(--backdrop);
  }
  .flag-canvas {
    display: block;
    width: 1200px;
    height: 1200px;
  }
  .brand-name {
    font-family: "Montserrat", sans-serif;
    font-weight: 700;
    fill: var(--text-white);
  }
</style>
</head>
<body>
<svg class="flag-canvas" viewBox="0 0 1200 1200" xmlns="http://www.w3.org/2000/svg">
  <defs>
    <linearGradient id="blueFill" x1="0" y1="0" x2="1" y2="1">
      <stop offset="0" stop-color="var(--flag-blue)"/>
      <stop offset="1" stop-color="var(--flag-blue-deep)"/>
    </linearGradient>
    <linearGradient id="photoTone" x1="0" y1="0" x2="0" y2="1">
      <stop offset="0" stop-color="var(--photo-top)"/>
      <stop offset="0.5" stop-color="var(--photo-mid)"/>
      <stop offset="1" stop-color="var(--photo-low)"/>
    </linearGradient>
    <clipPath id="flagShape">
      <path d="M430,1050 L430,420 C430,260 560,160 770,150 L770,1050 Z"/>
    </clipPath>
  </defs>

  <g class="feather-flag" clip-path="url(#flagShape)">
    <rect class="flag-top" x="420" y="140" width="360" height="360" fill="var(--flag-black)"/>
    <rect class="flag-body" x="420" y="492" width="360" height="570" fill="url(#blueFill)"/>

    <rect class="site-photo" x="470" y="287" width="258" height="250"
          fill="url(#photoTone)" role="img"
          aria-label="Photo of an excavator on a construction site at sunset"/>

    <g class="brand-lockup">
      <rect class="brand-mark" x="640" y="925" width="40" height="40" fill="var(--text-white)"/>
      <text class="brand-name brand-name--main" transform="translate(680,905) rotate(-90)" font-size="72" textLength="228" lengthAdjust="spacing">MESA</text>
      <text class="brand-name brand-name--sub" transform="translate(703,905) rotate(-90)" font-size="14" textLength="228" lengthAdjust="spacing">EQUIPMENT RENTALS</text>
    </g>
  </g>

  <path class="flag-sleeve" d="M430,1050 L430,420 C430,260 560,160 770,150" fill="none" stroke="var(--flag-sleeve)" stroke-width="10" stroke-linecap="round"/>
  <path class="flag-edge" d="M430,1050 L770,1050 L770,150" fill="none" stroke="var(--flag-sleeve)" stroke-width="3"/>
</svg>
</body>
</html>
```